We need a web page design for a new company called "Brambel". We provide an innovative music sharing mobile application that allows music listeners to share their music without paying for a monthly subscription. We would like to incorporate the attached logo and color scheme. The final design should communicate music gifting and sharing.

Industry/Entity Type

It Company

```html
<!DOCTYPE html>
<html lang="en">
<head>
<meta charset="utf-8">
<title>Brambel – share the sound</title>
<link rel="stylesheet" href="https://fonts.googleapis.com/css2?family=Lato:wght@400;700;900&family=Oswald:wght@400;500&family=Courgette&display=swap">
<style>
:root{
  --green:#5ba500;
  --green-dark:#4a8a00;
  --green-light:#6fbf0c;
  --ink:#222;
  --text:#555;
  --grey-band:#efefef;
  --grey-btn:#666;
  --footer:#333;
  --white:#fff;
}
*{box-sizing:border-box;margin:0;padding:0}
html,body{width:1200px;height:2275px;overflow:hidden}
body{position:relative;background:var(--white);font-family:"Lato",Arial,sans-serif;color:var(--text)}

/* header */
.site-header{position:absolute;left:0;top:0;width:1200px;height:99px;background:var(--green)}
.brand{position:absolute;left:133px;top:14px;display:flex;align-items:center;gap:12px}
.brand-dot{width:46px;height:46px;border-radius:50%;background:var(--white)}
.brand-name{font-family:"Lato",sans-serif;font-weight:700;font-size:46px;color:var(--white);line-height:1}
.brand-tag{position:absolute;left:191px;top:66px;font-size:15px;color:var(--white)}
.search{position:absolute;left:455px;top:38px;width:231px;height:27px;background:var(--white);display:flex}
.search span{flex:1;font-size:13px;color:#444;padding:6px 8px}
.search i{width:27px;height:27px;background:#222;display:flex;align-items:center;justify-content:center}
.main-nav{position:absolute;left:749px;top:30px;display:flex;align-items:center;gap:22px;font-size:21px;color:var(--white);font-weight:700}
.main-nav .upload{background:#222;padding:8px 12px}

/* hero */
.hero{position:absolute;left:0;top:99px;width:1200px;height:438px;background:radial-gradient(circle at 48% 35%,#f0b35a 0,#b8642a 18%,#7a3414 45%,#4a1d0b 100%)}
.hero-title{position:absolute;left:125px;top:140px;width:390px;font-family:"Courgette",cursive;font-size:35px;font-weight:400;line-height:56px;color:var(--white);text-align:center}
.hero-dots{position:absolute;left:231px;top:402px;display:flex;gap:12px}
.hero-dots span{width:20px;height:20px;border-radius:50%;background:var(--white)}
.hero-dots span.on{background:var(--green)}

/* features */
.features{position:absolute;left:0;top:537px;width:1200px;height:354px;background:var(--grey-band);border-top:4px solid #dcdcdc}
.feature{position:absolute;top:36px;width:230px;text-align:center}
.feature-icon{width:138px;height:138px;margin:0 auto;border-radius:50%;border:4px solid #222;background:#cfcfcf;display:flex;align-items:center;justify-content:center;box-shadow:inset 0 0 0 6px var(--white)}
.feature-icon.active{background:var(--green)}
.feature h3{margin-top:26px;font-size:18px;font-weight:700;color:var(--ink)}
.feature p{margin-top:18px;font-size:13px;line-height:19px;color:#444}

/* trending */
.section-title{position:absolute;left:0;top:918px;width:1200px;text-align:center;font-size:28px;font-weight:700;color:var(--green)}
.category{position:absolute;left:131px;top:982px;width:233px;height:313px;background:var(--white)}
.category-head{height:46px;background:#000;color:var(--white);font-size:25px;font-weight:700;padding:6px 12px}
.cat-item{height:28px;background:var(--green);border-bottom:2px solid var(--white);color:var(--white);font-size:13px;font-weight:700;padding:6px 14px;display:flex;justify-content:space-between;align-items:center}
.cat-item.sub{background:var(--green-light);padding-left:16px}
.cat-item b{width:18px;height:18px;border-radius:50%;background:var(--white);display:flex;align-items:center;justify-content:center}
.poster{position:absolute;left:131px;top:1321px;width:233px;height:310px;background:linear-gradient(160deg,#1a1a1a,#3b2a14 60%,#111)}
.card{position:absolute;width:205px;height:311px;border:2px solid #bbb;background:var(--white);padding:5px}
.card-img{height:169px}
.img-a{background:linear-gradient(180deg,#7c7f80 0,#2a2a2a 55%,#111 100%)}
.img-b{background:radial-gradient(circle at 50% 40%,#7a3b8c 0,#2c1440 55%,#0d0814 100%)}
.img-c{background:radial-gradient(circle at 50% 40%,#8fb7cf 0,#355a74 45%,#111a22 100%)}
.card h4{margin-top:8px;font-size:16px;line-height:20px;color:var(--green);font-weight:700;height:42px}
.card p{margin-top:8px;font-size:12.5px;line-height:18px;color:#444}
.card-actions{position:absolute;left:8px;bottom:10px;display:flex;gap:10px}
.card-actions span{height:20px;font-size:13px;font-weight:700;color:var(--white);display:flex;align-items:center;justify-content:center}
.btn-gift{width:52px;background:var(--grey-btn)}
.btn-share{width:76px;background:var(--green)}

/* CTA */
.cta{position:absolute;left:131px;top:1655px;width:936px;height:89px;background:var(--green);display:flex;align-items:center;padding-left:18px}
.cta p{font-family:"Oswald",sans-serif;font-size:29px;line-height:35px;color:var(--white);width:600px}
.cta-btn{position:absolute;right:30px;top:12px;width:226px;height:64px;background:#000;border:3px solid #555;border-radius:14px;font-family:"Oswald",sans-serif;font-size:33px;color:var(--white);display:flex;align-items:center;justify-content:center}

/* news */
.news-title{position:absolute;left:161px;top:1775px;font-size:19px;font-weight:700;color:#333}
.news-title em{font-style:normal;color:var(--green)}
.news-arrows{position:absolute;left:990px;top:1780px;display:flex;gap:6px}
.news-arrows span{width:20px;height:18px;background:#eee;border:1px solid #ccc;display:flex;align-items:center;justify-content:center}
.news-rule{position:absolute;left:161px;top:1810px;width:878px;height:1px;background:#ddd}
.news{position:absolute;left:161px;top:1820px;width:878px;height:148px;background:var(--white);border:1px solid #e3e3e3;box-shadow:0 18px 16px -12px rgba(0,0,0,.35);display:flex}
.news-item{flex:1;display:flex;gap:12px;padding:14px 10px;border-right:1px solid #e3e3e3}
.news-item:last-child{border-right:0}
.news-thumb{width:98px;height:110px;flex:none;border:3px solid #ddd}
.thumb-a{background:linear-gradient(135deg,#e04a3a,#f2a0b8 50%,#c23060)}
.thumb-b{background:radial-gradient(circle,#e8b020,#8a1a10 70%,#200)}
.thumb-c{background:linear-gradient(135deg,#2c3e50,#7a8a9a 50%,#1a1a1a)}
.news-item h5{font-size:14px;font-weight:400;color:#333}
.news-item time{display:block;margin-top:4px;font-size:11px;color:var(--green)}
.news-item p{margin-top:4px;font-size:12px;line-height:17px;color:#444}

/* footer */
.site-footer{position:absolute;left:0;top:2019px;width:1200px;height:218px;background:var(--footer);color:#ddd}
.foot-col{position:absolute;top:20px}
.foot-col h6{font-size:20px;font-weight:400;color:var(--white);padding-bottom:6px;border-bottom:1px solid #555;width:160px}
.quick li{list-style:none;font-size:13px;line-height:25px}
.quick ul{margin-top:10px}
.newsletter p{margin-top:12px;font-size:13px;line-height:20px;width:220px}
.email-field{margin-top:14px;width:214px;height:26px;background:#666;font-size:12px;color:#eee;padding:6px 8px}
.subscribe{margin-top:16px;width:88px;height:26px;background:var(--green);color:var(--white);font-size:12px;font-weight:700;display:flex;align-items:center;justify-content:center}
.social li{list-style:none;display:flex;align-items:center;gap:10px;font-size:14px;height:34px}
.social ul{margin-top:10px}
.social li b{width:22px;height:22px;background:#666}
.foot-brand{position:absolute;left:930px;top:96px;display:flex;align-items:center;gap:10px}
.foot-brand i{width:40px;height:40px;border-radius:50%;background:var(--white)}
.foot-brand span{font-size:30px;font-weight:700;color:var(--white)}
.divider{position:absolute;top:20px;width:1px;height:180px;background:#444}
.copyright{position:absolute;left:0;top:2237px;width:1200px;height:38px;background:var(--green);color:var(--white);font-size:13px;display:flex;align-items:center;justify-content:center}
</style>
</head>
<body>

<header class="site-header">
  <div class="brand"><span class="brand-dot"></span><span class="brand-name">Brambel</span></div>
  <div class="brand-tag">share the sound</div>
  <div class="search"><span>Search</span><i><svg width="14" height="14" viewBox="0 0 14 14"><circle cx="6" cy="6" r="4" fill="none" stroke="#fff" stroke-width="2"/><line x1="9" y1="9" x2="13" y2="13" stroke="#fff" stroke-width="2"/></svg></i></div>
  <nav class="main-nav"><span>People</span><span>Sign Up</span><span>Login</span><span class="upload">Upload</span></nav>
</header>

<section class="hero" role="img" aria-label="Warm amber photo of a singer lit from behind with floating feathers and music notes">
  <h1 class="hero-title">Lorem ipsum dolor<br>sit amet consectetuer<br>adipiscing elit</h1>
  <div class="hero-dots"><span class="on"></span><span></span><span></span><span></span></div>
</section>

<section class="features">
  <div class="feature" style="left:128px">
    <div class="feature-icon active"><svg width="70" height="70" viewBox="0 0 70 70"><path d="M35 6 L52 26 H42 V42 H28 V26 H18 Z" fill="#222"/><rect x="8" y="46" width="54" height="16" rx="2" fill="#222"/><circle cx="52" cy="54" r="3" fill="#5ba500"/></svg></div>
    <h3>UPLOAD MUSIC &amp; AUDIO</h3>
    <p>Lorem ipsum dolor sit amet consectetuer adipiscing elit sed diam nonummy nibh euismod tincidunt ut laoreet</p>
  </div>
  <div class="feature" style="left:370px">
    <div class="feature-icon"><svg width="74" height="70" viewBox="0 0 74 70"><path d="M6 25 H20 L38 10 V60 L20 45 H6 Z" fill="#222"/><path d="M46 24 Q52 35 46 46 M54 17 Q64 35 54 53 M62 10 Q76 35 62 60" fill="none" stroke="#222" stroke-width="5" stroke-linecap="round"/></svg></div>
    <h3>LISTEN &amp; DISCOVER</h3>
    <p>Lorem ipsum dolor sit amet consectetuer adipiscing elit sed diam nonummy nibh euismod tincidunt ut laoreet</p>
  </div>
  <div class="feature" style="left:611px">
    <div class="feature-icon"><svg width="80" height="70" viewBox="0 0 80 70"><circle cx="50" cy="22" r="13" fill="#222"/><path d="M28 60 Q30 38 50 38 Q70 38 72 60 Z" fill="#222"/><circle cx="30" cy="28" r="12" fill="#222" stroke="#cfcfcf" stroke-width="3"/><path d="M8 64 Q10 44 30 44 Q50 44 52 64 Z" fill="#222" stroke="#cfcfcf" stroke-width="3"/></svg></div>
    <h3>CONNECT</h3>
    <p>Lorem ipsum dolor sit amet consectetuer adipiscing elit sed diam nonummy nibh euismod tincidunt ut laoreet</p>
  </div>
  <div class="feature" style="left:852px">
    <div class="feature-icon"><svg width="70" height="70" viewBox="0 0 70 70"><line x1="50" y1="15" x2="20" y2="35" stroke="#222" stroke-width="5"/><line x1="50" y1="55" x2="20" y2="35" stroke="#222" stroke-width="5"/><circle cx="50" cy="15" r="10" fill="#222"/><circle cx="50" cy="55" r="10" fill="#222"/><circle cx="20" cy="35" r="10" fill="#222"/></svg></div>
    <h3>SHARE</h3>
    <p>Lorem ipsum dolor sit amet consectetuer adipiscing elit sed diam nonummy nibh euismod tincidunt ut laoreet</p>
  </div>
</section>

<h2 class="section-title">Trending Music &amp; Audio</h2>

<aside class="category">
  <div class="category-head">Category</div>
  <div class="cat-item">Lorem ipsum dolor sit<b><svg width="10" height="8" viewBox="0 0 10 8"><path d="M0 0H10L5 7Z" fill="#5ba500"/></svg></b></div>
  <div class="cat-item sub">&gt; Lorem ipsum dolor sit</div>
  <div class="cat-item sub">&gt; Lorem ipsum dolor sit</div>
  <div class="cat-item sub">&gt; Lorem ipsum dolor sit</div>
  <div class="cat-item sub">&gt; Lorem ipsum dolor sit</div>
  <div class="cat-item sub">&gt; Lorem ipsum dolor sit</div>
  <div class="cat-item">Lorem ipsum dolor sit<b><svg width="8" height="10" viewBox="0 0 8 10"><path d="M0 0V10L7 5Z" fill="#5ba500"/></svg></b></div>
  <div class="cat-item">Lorem ipsum dolor sit<b><svg width="8" height="10" viewBox="0 0 8 10"><path d="M0 0V10L7 5Z" fill="#5ba500"/></svg></b></div>
  <div class="cat-item">Lorem ipsum dolor sit<b><svg width="8" height="10" viewBox="0 0 8 10"><path d="M0 0V10L7 5Z" fill="#5ba500"/></svg></b></div>
</aside>

<div class="poster" role="img" aria-label="Event poster illustration with a beer glass, quill and radio promoting a music night"></div>

<article class="card" style="left:394px;top:982px"><div class="card-img img-a" role="img" aria-label="Dark audiobook cover artwork with a ruined city skyline"></div><h4>Ashfall Z Audio Book</h4><p>Lorem ipsum dolor sit amet consectetuer adipiscing</p><div class="card-actions"><span class="btn-gift">Gift</span><span class="btn-share">Share</span></div></article>
<article class="card" style="left:628px;top:982px"><div class="card-img img-b" role="img" aria-label="DJ performing under purple club lights"></div><h4>Rex Vale Tribute To Dario Sto...</h4><p>Lorem ipsum dolor sit amet consectetuer adipiscing</p><div class="card-actions"><span class="btn-gift">Gift</span><span class="btn-share">Share</span></div></article>
<article class="card" style="left:862px;top:982px"><div class="card-img img-c" role="img" aria-label="DJ at decks under blue stage lights"></div><h4>Deep Room Halifax</h4><p>Lorem ipsum dolor sit amet consectetuer adipiscing</p><div class="card-actions"><span class="btn-gift">Gift</span><span class="btn-share">Share</span></div></article>

<article class="card" style="left:394px;top:1320px"><div class="card-img img-a" role="img" aria-label="Dark audiobook cover artwork with a ruined city skyline"></div><h4>Ashfall Z Audio Book</h4><p>Lorem ipsum dolor sit amet consectetuer adipiscing</p><div class="card-actions"><span class="btn-gift">Gift</span><span class="btn-share">Share</span></div></article>
<article class="card" style="left:628px;top:1320px"><div class="card-img img-b" role="img" aria-label="DJ performing under purple club lights"></div><h4>Rex Vale Tribute To Dario Sto...</h4><p>Lorem ipsum dolor sit amet consectetuer adipiscing</p><div class="card-actions"><span class="btn-gift">Gift</span><span class="btn-share">Share</span></div></article>
<article class="card" style="left:862px;top:1320px"><div class="card-img img-c" role="img" aria-label="DJ at decks under blue stage lights"></div><h4>Deep Room Halifax</h4><p>Lorem ipsum dolor sit amet consectetuer adipiscing</p><div class="card-actions"><span class="btn-gift">Gift</span><span class="btn-share">Share</span></div></article>

<section class="cta">
  <p>So are you ready to discover new music and sounds and share them with the world?</p>
  <span class="cta-btn">SIGN UP NOW!</span>
</section>

<h2 class="news-title">Latest <em>News</em></h2>
<div class="news-arrows"><span><svg width="6" height="8" viewBox="0 0 6 8"><path d="M6 0V8L0 4Z" fill="#333"/></svg></span><span><svg width="6" height="8" viewBox="0 0 6 8"><path d="M0 0V8L6 4Z" fill="#333"/></svg></span></div>
<div class="news-rule"></div>
<section class="news">
  <div class="news-item"><div class="news-thumb thumb-a" role="img" aria-label="Colourful festival photo"></div><div><h5>Lorem ipsum dolor</h5><time>November 3, 2014 at 4:10 pm</time><p>Lorem ipsum dolor sit am consectetuer adipiscingi elit, sed diam nonummy nibh euismod tincid.</p></div></div>
  <div class="news-item"><div class="news-thumb thumb-b" role="img" aria-label="Music news graphic in gold and red"></div><div><h5>Lorem ipsum dolor</h5><time>November 3, 2014 at 4:10 pm</time><p>Lorem ipsum dolor sit am consectetuer adipiscingi elit, sed diam nonummy nibh euismod tincid.</p></div></div>
  <div class="news-item"><div class="news-thumb thumb-c" role="img" aria-label="Band photo at a keyboard"></div><div><h5>Lorem ipsum dolor</h5><time>November 3, 2014 at 4:10 pm</time><p>Lorem ipsum dolor sit am consectetuer adipiscingi elit, sed diam nonummy nibh euismod tincid.</p></div></div>
</section>

<footer class="site-footer">
  <div class="foot-col quick" style="left:131px"><h6>Quick Links</h6><ul><li>› About Us</li><li>› People</li><li>› Sign Up</li><li>› Login</li><li>› Upload</li></ul></div>
  <div class="divider" style="left:340px"></div>
  <div class="foot-col newsletter" style="left:387px"><h6>Newsletter</h6><p>Signup with us and get update in your inbox.</p><div class="email-field">Email address</div><div class="subscribe">SUBSCRIBE</div></div>
  <div class="divider" style="left:670px"></div>
  <div class="foot-col social" style="left:711px"><h6>Follow Us On</h6><ul><li><b></b>Facelink</li><li><b></b>Chirper</li><li><b></b>ViewTube</li><li><b></b>ProNet</li></ul></div>
  <div class="divider" style="left:895px"></div>
  <div class="foot-brand"><i></i><span>Brambel</span></div>
</footer>
<div class="copyright">© 2014 BrambelMusic. All Rights Reserved.</div>

</body>
</html>
```